Volbrey Inc Business Card

Looking to get an updated business card for a Contract Machining company (www.volbreyinc.example) - looking for a clean design the portrays the technical nature of the business - colors can follow the website design and be in any combination that makes sense (red black, white, metallic or silver) - logos attached for use also. Would like space for: Name, title, business phone (555 214-3086), cell phone , website (www.volbreyinc.example) - possibly QR code could be integrated for website (designer choice), business address - 418 Harlow Bend, Merrow Falls, OH 48199 (cards will be for 4 employees, I will either need to modify a template or I can provide individual information)
Target Market(s)
Aerospace, defense and medical device manufacturing companies that need machining
Industry/Entity Type
Machining for aerospace, defense, medical
Contact Information for Business Card
Name, Title, Business Phone, Cell Phone, email, business website and business address
Look and feel

```html
<!DOCTYPE html>
<html lang="en">
<head>
<meta charset="utf-8">
<title>Volbrey Inc Business Card</title>
<link href="https://fonts.googleapis.com/css2?family=Montserrat:wght@400;500;700;800&display=swap" rel="stylesheet">
<style>
  :root {
    --backdrop: #2e2926;
    --card-black: #1c1c1d;
    --card-charcoal: #262627;
    --brand-red: #c8202c;
    --band-red: #c23a41;
    --band-shadow: #8e2229;
    --text-white: #f2f2f2;
  }
  * { margin: 0; padding: 0; box-sizing: border-box; }
  html, body {
    width: 1200px; height: 716px; overflow: hidden;
    background: var(--backdrop);
    font-family: "Montserrat", sans-serif;
  }
  .stage { position: relative; width: 1200px; height: 716px; }

  .card {
    position: absolute; top: 209px;
    width: 520px; height: 298px;
    border-radius: 4px;
    box-shadow: 0 10px 30px rgba(0,0,0,.45);
    overflow: hidden;
  }

  /* Front */
  .card-front {
    left: 50px;
    background: var(--card-black);
    border-bottom: 4px solid var(--brand-red);
  }
  .front-wordmark {
    position: absolute; left: 0; right: 0; top: 118px;
    text-align: center;
    color: var(--brand-red);
    font-weight: 800; font-size: 50px; letter-spacing: 1px;
    text-transform: uppercase;
  }

  /* Back */
  .card-back {
    left: 630px;
    background: linear-gradient(160deg, var(--card-charcoal) 0%, var(--card-black) 100%);
    border: 2px solid var(--brand-red);
  }
  .side-band {
    position: absolute; left: 34px; top: 0; bottom: 0; width: 70px;
    background: var(--band-red);
    box-shadow: 6px 0 10px rgba(0,0,0,.45);
  }
  .band-disc {
    position: absolute; left: 30px; top: 22px;
    width: 78px; height: 78px; border-radius: 50%;
    background: var(--band-red);
    border: 5px solid var(--band-shadow);
  }
  .back-wordmark {
    position: absolute; left: 124px; top: 48px;
    color: var(--brand-red);
    font-weight: 800; font-size: 34px; letter-spacing: 1px;
    text-transform: uppercase;
  }
  .divider {
    position: absolute; height: 1px; background: var(--brand-red);
  }
  .divider-top { left: 124px; right: 20px; top: 132px; }
  .divider-title { left: 330px; right: 20px; top: 218px; }

  .contact-list {
    position: absolute; left: 124px; top: 146px;
    list-style: none;
    color: var(--text-white); font-size: 12px; font-weight: 500;
  }
  .contact-list li { display: flex; align-items: center; gap: 7px; height: 19px; }
  .contact-list svg { width: 10px; height: 10px; flex: none; }

  .person {
    position: absolute; right: 26px; top: 164px; text-align: right;
  }
  .person-name {
    color: var(--brand-red); font-weight: 700; font-size: 19px;
    text-transform: uppercase; letter-spacing: .5px;
  }
  .person-title {
    color: var(--text-white); font-size: 12px; font-weight: 500;
    text-transform: uppercase; letter-spacing: 1px; margin-top: 2px;
  }
  .address {
    position: absolute; right: 26px; bottom: 22px; text-align: right;
    color: var(--text-white); font-size: 13px; font-weight: 500; line-height: 1.45;
    font-style: normal;
  }
  .edge-tab {
    position: absolute; right: 0; top: 188px; width: 5px; height: 28px;
    background: var(--brand-red);
  }
</style>
</head>
<body>
<main class="stage">
  <section class="card card-front" aria-label="Card front">
    <div class="front-wordmark">Volbrey Inc</div>
  </section>

  <section class="card card-back" aria-label="Card back">
    <div class="side-band"></div>
    <div class="band-disc"></div>
    <div class="back-wordmark">Volbrey Inc</div>
    <div class="divider divider-top"></div>

    <ul class="contact-list">
      <li>
        <svg viewBox="0 0 10 10"><path d="M2 1 L4 1 L4.6 3 L3.4 3.8 Q4.4 5.8 6.2 6.6 L7 5.4 L9 6 L9 8 Q8 9.2 6.5 8.6 Q2.2 6.8 1 2.6 Q1 1.5 2 1Z" fill="var(--brand-red)"/></svg>
        555 214-3086
      </li>
      <li>
        <svg viewBox="0 0 10 10"><rect x="2.5" y="0.5" width="5" height="9" rx="1" fill="none" stroke="var(--brand-red)"/><circle cx="5" cy="7.8" r=".6" fill="var(--brand-red)"/></svg>
        555-380-7421
      </li>
      <li>
        <svg viewBox="0 0 10 10"><rect x="0.5" y="2" width="9" height="6" fill="none" stroke="var(--brand-red)"/><path d="M0.5 2 L5 5.5 L9.5 2" fill="none" stroke="var(--brand-red)"/></svg>
        info@volbreyinc.example
      </li>
      <li>
        <svg viewBox="0 0 10 10"><circle cx="5" cy="5" r="4.3" fill="none" stroke="var(--brand-red)"/><ellipse cx="5" cy="5" rx="1.8" ry="4.3" fill="none" stroke="var(--brand-red)"/><path d="M0.7 5 H9.3" stroke="var(--brand-red)"/></svg>
        www.volbreyinc.example
      </li>
    </ul>

    <div class="person">
      <div class="person-name">Daniel Corwin</div>
      <div class="person-title">Director</div>
    </div>
    <div class="divider divider-title"></div>

    <address class="address">
      418 Harlow Bend,<br>Merrow Falls, OH 48199
    </address>
    <div class="edge-tab"></div>
  </section>
</main>
</body>
</html>
```